WordPress webdesign with coding for our company BRISK The Answer

BRISK The Answer is a payrolling company such as Montaval Wages (one of our competitor https://www.montaval-wages.ch/fr/). We need to set up our website in both languages (Fr and Eng). Our logo is enclosed.
we would like something simple explaining what is payrolling in Graph and wording, who we are and a contact page. you can also take some example if needed from our mother company BRISK The Horizon (www.briskthehorizon.ch) or our sister company (www.briskyourstride.ch). we would like to keep the color panel of our logo (ref. Black = PANTONE P Process Black C
Pink = PANTONE P Process Magenta C
Grey = PANTONE 430 C) as the driver of the website.

```html
<!DOCTYPE html>
<html lang="en">
<head>
<meta charset="utf-8">
<title>BRISK The Answer – Payrolling</title>
<link href="https://fonts.googleapis.com/css2?family=Poppins:ital,wght@0,400;0,500;0,600;0,700;1,400&display=swap" rel="stylesheet">
<style>
:root{
  --pink:#e6117f;
  --pink-soft:#f07ab6;
  --black:#1a1819;
  --ink:#222;
  --text:#3a3a3a;
  --grey:#efeeee;
  --grey-mid:#8a8d8f;
  --white:#fff;
}
*{box-sizing:border-box;margin:0;padding:0}
html,body{width:1200px;height:4373px;overflow:hidden}
body{position:relative;background:var(--white);font-family:'Poppins',sans-serif;color:var(--ink)}
.abs{position:absolute}
.btn{position:absolute;display:flex;align-items:center;justify-content:center;background:var(--pink);color:var(--white);border-radius:26px;font-size:16px;font-weight:500;box-shadow:0 6px 14px rgba(230,17,127,.35)}
.logo-pill{position:absolute;background:var(--white);border-radius:40px;display:flex;align-items:center;justify-content:center;font-weight:700;color:var(--black);font-size:22px;letter-spacing:1px;box-shadow:0 0 0 4px rgba(255,255,255,.6)}
/* header */
.nav{left:75px;top:31px;width:1050px;height:78px;background:rgba(40,40,40,.82);border-radius:40px}
.nav-links{left:352px;top:31px;height:78px;display:flex;align-items:center;gap:38px;font-size:14px;color:var(--white)}
.nav-links .active{color:var(--pink);font-weight:600}
.nav-tools{left:985px;top:31px;height:78px;display:flex;align-items:center;gap:36px;color:var(--white);font-size:13px}
/* hero */
.hero-title{left:75px;top:250px;font-size:50px;font-weight:400;letter-spacing:1px;color:var(--black)}
.hero-title b{color:var(--pink);font-weight:700}
.hero-text{left:75px;top:316px;width:560px;font-size:18px;line-height:23px;color:var(--black)}
/* services */
.services{left:75px;top:582px;width:1050px;height:326px;background:var(--white);border-radius:22px;box-shadow:0 4px 22px rgba(0,0,0,.12)}
.h2{font-size:32px;font-weight:600;color:var(--black)}
.col3{position:absolute;width:320px;text-align:center}
.col3 h3{color:var(--pink);font-size:21px;font-weight:600;margin-bottom:12px}
.col3 p{font-size:13.5px;line-height:24px;color:var(--text)}
/* about */
.about-sub{color:var(--pink);font-size:23px;line-height:33px;font-weight:500}
.body-p{font-size:14.5px;line-height:26.5px;color:var(--text)}
/* figures */
.fig{position:absolute;top:2091px;width:241px;height:183px;background:var(--white);border-radius:20px;box-shadow:0 4px 16px rgba(0,0,0,.08);text-align:center;padding-top:46px}
.fig b{display:block;color:var(--pink);font-size:38px;font-weight:700;line-height:46px}
.fig span{font-size:17px;color:var(--black)}
/* tabs */
.tab{position:absolute;top:2447px;height:73px;padding:14px 0 0 32px;font-size:17px;font-weight:600;line-height:26px;color:var(--black);border-left:6px solid var(--pink)}
.ticks li{list-style:none;display:flex;align-items:center;gap:14px;font-size:14.5px;color:var(--text);height:36.5px}
.tick{width:14px;height:14px;border-radius:50%;background:var(--pink);display:flex;align-items:center;justify-content:center}
/* why */
.why-icon{position:absolute;top:3213px;width:64px;height:64px;border-radius:50%;background:var(--pink-soft);display:flex;align-items:center;justify-content:center}
/* testimonial */
.quote{left:200px;top:3548px;width:800px;text-align:center;font-style:italic;font-size:22px;line-height:34px;color:var(--text)}
/* footer */
.f-col{position:absolute;top:3992px;color:var(--white)}
.f-col h4{font-size:22px;font-weight:600;margin-bottom:16px}
.f-col li{list-style:none;font-size:14.5px;line-height:36px;color:#e8e8e8}
.social{position:absolute;top:4175px;width:40px;height:40px;border-radius:50%;background:#ececec}
.bottom-bar{left:75px;top:4263px;width:1050px;height:78px;background:var(--pink);border-radius:40px}
</style>
</head>
<body>

<!-- HERO -->
<svg class="abs" style="left:0;top:0" width="1200" height="703" role="img" aria-label="Photo of a professional woman working on a laptop and tablet in a bright office">
  <defs>
    <linearGradient id="heroGrad" x1="0" y1="0" x2="1" y2="0.4">
      <stop offset="0" stop-color="#eef2f6"/>
      <stop offset="0.45" stop-color="#d9e1ea"/>
      <stop offset="0.7" stop-color="#9aa8b4"/>
      <stop offset="1" stop-color="#5e6a74"/>
    </linearGradient>
  </defs>
  <path d="M0 0H1200V703C1150 703 1125 680 1125 640V636H60C25 636 0 612 0 580Z" fill="url(#heroGrad)"/>
</svg>

<div class="abs nav"></div>
<div class="logo-pill" style="left:75px;top:31px;width:248px;height:78px">BRISK The Answer</div>
<nav class="abs nav-links">
  <span class="active">Home</span><span>About Us</span><span>Solutions</span><span>Blog</span><span>Contact Us</span>
</nav>
<div class="abs nav-tools">
  <svg width="16" height="16" viewBox="0 0 16 16"><circle cx="8" cy="8" r="6.5" fill="none" stroke="#fff" stroke-width="1.5"/><circle cx="8" cy="7" r="2" fill="#fff"/></svg>
  <span style="display:flex;align-items:center;gap:6px"><svg width="15" height="15" viewBox="0 0 16 16"><circle cx="8" cy="8" r="6.5" fill="none" stroke="#fff" stroke-width="1.5"/><path d="M1.5 8h13M8 1.5c3 3.5 3 9.5 0 13M8 1.5c-3 3.5-3 9.5 0 13" fill="none" stroke="#fff" stroke-width="1.2"/></svg>En ▾</span>
</div>

<h1 class="abs hero-title"><b>BRISK</b> THE ANSWER</h1>
<p class="abs hero-text">Excepteur sint occaecat cupidatat non proident, sunt in culpa qui officia deserunt mollit anim id est laborum enim ipsam voluptatem quia voluptas.</p>
<div class="btn" style="left:75px;top:409px;width:241px;height:49px">Discover Payrolling</div>

<!-- SERVICES -->
<section class="abs services">
  <h2 class="h2 abs" style="left:0;top:26px;width:1050px;text-align:center">Discover all Our Services</h2>
  <svg class="abs" style="left:150px;top:98px" width="70" height="70" viewBox="0 0 70 70" fill="none" stroke="#222" stroke-width="2"><circle cx="30" cy="20" r="12"/><path d="M10 62c0-14 8-22 20-22s20 8 20 22"/><circle cx="52" cy="50" r="10" stroke="#e6117f"/><path d="M52 44v12M49 47h5" stroke="#e6117f"/></svg>
  <svg class="abs" style="left:495px;top:98px" width="60" height="70" viewBox="0 0 60 70" fill="none" stroke="#222" stroke-width="2"><path d="M8 4h32l12 12v50H8z"/><path d="M40 4v12h12"/><path d="M30 24v34M36 30c-2-3-12-3-12 2s12 4 12 9-10 5-12 2" stroke="#e6117f"/></svg>
  <svg class="abs" style="left:835px;top:98px" width="72" height="70" viewBox="0 0 72 70" fill="none" stroke="#222" stroke-width="2"><rect x="18" y="4" width="36" height="30" rx="3"/><path d="M28 19l6 6 11-11" stroke="#e6117f"/><path d="M4 40h12l10 14h20l10-14h12M26 54l8-8 8 8"/></svg>
  <div class="col3" style="left:24px;top:186px"><h3>Payrolling</h3><p>Excepteur sint occaecat cupidatat<br>non proident, sunt in culpa qui officia dese<br>runt mollit anim id est laborum.</p></div>
  <div class="col3" style="left:365px;top:186px"><h3>Sourcing</h3><p>Excepteur sint occaecat cupidatat<br>non proident, sunt in culpa qui officia dese<br>runt mollit anim id est laborum.</p></div>
  <div class="col3" style="left:710px;top:186px"><h3>Payroll Outsourcing</h3><p>Excepteur sint occaecat cupidatat<br>non proident, sunt in culpa qui officia dese<br>runt mollit anim id est laborum.</p></div>
</section>

<!-- ABOUT -->
<h2 class="abs h2" style="left:75px;top:995px">About Payrolling</h2>
<p class="abs about-sub" style="left:75px;top:1054px;width:430px">Duis aute irure dolor in reprehend voluptate velit esse</p>
<p class="abs body-p" style="left:75px;top:1137px;width:430px">Nemo enim ipsam voluptatem quia voluptas sit aspernatur aut odit aut fugit, sed quia consequuntur magni dolores eos qui ratione voluptatem sequi nesciunt. Neque porro quisquam est, qui dolorem ipsum quia dolor sit amet, consectetur, adipisci velit, sed quia non numquam eius modi tempora incidunt ut labore et dolore magnam aliquam quaerat voluptatem.</p>
<div class="btn" style="left:75px;top:1348px;width:241px;height:49px">Discover Payrolling</div>
<div class="abs" role="img" aria-label="HR management dashboard shown on a tablet, with salary report, income and attrition charts" style="left:524px;top:993px;width:676px;height:412px;background:linear-gradient(90deg,#1d1a1c 0,#1d1a1c 10px,#5a2d52 10px,#5a2d52 110px,#ece6ee 110px);border-radius:22px 0 0 22px"></div>

<!-- WELCOME + FIGURES -->
<svg class="abs" style="left:0;top:1463px" width="1200" height="800">
  <path d="M0 130C0 110 20 100 60 100C300 80 700 40 1130 2C1170 -2 1200 10 1200 40V794H60C25 794 0 770 0 730Z" fill="#efeeee"/>
</svg>
<div class="abs" role="img" aria-label="Photo of a smiling man working on a laptop" style="left:0;top:1473px;width:560px;height:512px;background:radial-gradient(ellipse at 40% 45%,#c58a4c 0,#a56f3c 25%,#d9d6d2 55%,rgba(239,238,238,0) 75%)"></div>
<h2 class="abs" style="left:616px;top:1642px;font-size:33px;line-height:40px;font-weight:600;color:var(--black)">Welcome to <span style="color:var(--pink)">Brisk</span><br><span style="font-weight:400">The Answer</span></h2>
<p class="abs body-p" style="left:616px;top:1741px;width:515px">Nemo enim ipsam voluptatem quia voluptas sit aspernatur aut odit aut fugit, sed quia consequuntur magni dolores eos qui ratione voluptatem sequi nesciunt. Neque porro quisquam est, qui dolorem ipsum quia dolor sit amet, consectetur, adipisci velit, sed quia non numquam eius modi tempora incidunt</p>
<div class="btn" style="left:616px;top:1904px;width:243px;height:49px">Discover Payrolling</div>

<h3 class="abs" style="left:77px;top:2022px;font-size:22px;font-weight:600;color:var(--black)">Some key figures</h3>
<div class="fig" style="left:75px"><b>500+</b><span>Corporate Clients</span></div>
<div class="fig" style="left:345px"><b>1400+</b><span>Active Consultants</span></div>
<div class="fig" style="left:614px"><b>23000+</b><span>Pay Slips in 2023</span></div>
<div class="fig" style="left:884px"><b>31</b><span>Employees</span></div>

<!-- DIGITAL TOOLS -->
<h2 class="abs h2" style="left:0;top:2358px;width:1234px;text-align:center">High-Performance and Secure Digital Tools</h2>
<div class="tab" style="left:255px;width:332px;background:#ececec">Consultant space | Managing<br>your activities</div>
<div class="tab" style="left:618px;width:332px;border-left-color:var(--grey-mid)">Consultant space | Managing<br>your activities</div>

<h3 class="abs" style="left:75px;top:2597px;font-size:18px;font-weight:600;color:var(--pink)">Nemo enim ipsam voluptatem quia voluptas sit</h3>
<p class="abs body-p" style="left:75px;top:2632px;width:470px;line-height:24px">Aspernatur aut odit aut fugit, sed quia consequuntur magni dolores eos qui ratione voluptatem sequi nesciunt.</p>
<ul class="abs ticks" style="left:75px;top:2690px">
  <li><span class="tick"><svg width="8" height="8" viewBox="0 0 8 8"><path d="M1 4l2 2 4-4" stroke="#fff" stroke-width="1.5" fill="none"/></svg></span>Neque porro quisquam est</li>
  <li><span class="tick"><svg width="8" height="8" viewBox="0 0 8 8"><path d="M1 4l2 2 4-4" stroke="#fff" stroke-width="1.5" fill="none"/></svg></span>Qui dolorem ipsum quia dolor sit amet, consectetur</li>
  <li><span class="tick"><svg width="8" height="8" viewBox="0 0 8 8"><path d="M1 4l2 2 4-4" stroke="#fff" stroke-width="1.5" fill="none"/></svg></span>Adipisci velitsed quia non numquam</li>
  <li><span class="tick"><svg width="8" height="8" viewBox="0 0 8 8"><path d="M1 4l2 2 4-4" stroke="#fff" stroke-width="1.5" fill="none"/></svg></span>Eius modi tempora incidunt</li>
</ul>
<div class="btn" style="left:77px;top:2861px;width:241px;height:51px">Discover Payrolling</div>
<div class="abs" role="img" aria-label="Wireframe of the consultant space dashboard with bar and line charts and activity tables" style="left:584px;top:2590px;width:541px;height:336px;border-radius:10px;background:linear-gradient(90deg,#1f3550 0,#1f3550 72px,#eef1f6 72px);box-shadow:0 4px 16px rgba(0,0,0,.1)"></div>

<!-- WHY CHOOSE US -->
<svg class="abs" style="left:0;top:3030px" width="1200" height="434">
  <path d="M0 110C0 90 15 80 40 78L1150 8C1180 6 1200 20 1200 45V380C1200 410 1180 432 1150 432H50C20 432 0 410 0 380Z" fill="#efeeee"/>
</svg>
<h2 class="abs h2" style="left:0;top:3139px;width:1200px;text-align:center">Why Choose Us?</h2>
<div class="why-icon" style="left:225px"><svg width="30" height="26" viewBox="0 0 30 26" fill="none" stroke="#fff" stroke-width="2.4"><rect x="4" y="3" width="22" height="15" rx="1"/><path d="M1 22h28"/></svg></div>
<div class="why-icon" style="left:569px"><svg width="28" height="26" viewBox="0 0 28 26" fill="#fff"><rect x="2" y="7" width="24" height="17" rx="2"/><rect x="10" y="2" width="8" height="6" rx="1" fill="none" stroke="#fff" stroke-width="2"/></svg></div>
<div class="why-icon" style="left:914px"><svg width="28" height="28" viewBox="0 0 28 28" fill="none" stroke="#fff" stroke-width="3"><path d="M4 24L16 12"/><path d="M14 6l8 8 3-3-8-8z" fill="#fff"/></svg></div>
<div class="col3" style="left:97px;top:3296px"><h3>Management</h3><p>Excepteur sint occaecat cupidatat<br>non proident, sunt in culpa qui officia dese<br>runt mollit anim id est laborum.</p></div>
<div class="col3" style="left:441px;top:3296px"><h3>Expertise</h3><p>Excepteur sint occaecat cupidatat<br>non proident, sunt in culpa qui officia dese<br>runt mollit anim id est laborum.</p></div>
<div class="col3" style="left:786px;top:3296px"><h3>Accompaniement</h3><p>Excepteur sint occaecat cupidatat<br>non proident, sunt in culpa qui officia dese<br>runt mollit anim id est laborum.</p></div>

<!-- TESTIMONIAL -->
<div class="abs" style="left:160px;top:3498px;font-size:110px;line-height:1;color:var(--pink-soft);font-family:Georgia,serif">“</div>
<div class="abs" style="left:980px;top:3640px;font-size:110px;line-height:1;color:var(--pink-soft);font-family:Georgia,serif">”</div>
<p class="abs quote">“ Nemo enim ipsam voluptatem quia voluptas sit aspernatur aut odit aut fugit, sed quia consequuntur magni dolores eos qui ratione voluptatem sequi nesciunt..”</p>
<p class="abs" style="left:0;top:3672px;width:1200px;text-align:center;color:var(--pink);font-weight:600;font-size:14px">MATHILDE R.</p>
<p class="abs" style="left:0;top:3697px;width:1200px;text-align:center;font-size:14px;color:var(--text)">Project Manager</p>
<svg class="abs" style="left:562px;top:3758px" width="78" height="14"><circle cx="7" cy="7" r="6" fill="#222"/><circle cx="27" cy="7" r="6" fill="#999"/><circle cx="47" cy="7" r="6" fill="#999"/><circle cx="67" cy="7" r="6" fill="#999"/></svg>

<!-- FOOTER -->
<svg class="abs" style="left:0;top:3825px" width="1200" height="548">
  <path d="M0 175C0 150 20 135 50 132L1150 2C1180 -1 1200 15 1200 40V548H0Z" fill="#1a1819"/>
</svg>
<div class="f-col" style="left:73px"><h4>Company</h4><ul><li>Excepteur sint occaecat</li><li>Cupidatat non</li><li>Proident</li><li>Tempor incididunt</li><li>Dolore magna</li></ul></div>
<div class="f-col" style="left:344px"><h4>Solutions</h4><ul><li>Excepteur sint occaecat</li><li>Cupidatat non</li><li>Proident</li><li>Tempor incididunt</li><li>Dolore magna</li></ul></div>
<div class="f-col" style="left:616px"><h4>Resources</h4><ul><li>Excepteur sint occaecat</li><li>Cupidatat non</li><li>Proident</li><li>Tempor incididunt</li><li>Dolore magna</li></ul></div>
<div class="f-col" style="left:884px"><h4>Contact Us</h4><ul style="line-height:26px"><li style="line-height:26px">Excepteur sint occaecat<br>upidatat non</li><li>+41 22 555 0148</li><li style="line-height:28px">hello@brisktheanswer.ch</li></ul></div>
<span class="social" style="left:886px;background:var(--pink)" role="img" aria-label="Social network link"></span>
<span class="social" style="left:940px" role="img" aria-label="Social network link"></span>
<span class="social" style="left:993px" role="img" aria-label="Social network link"></span>
<span class="social" style="left:1046px" role="img" aria-label="Social network link"></span>

<div class="abs bottom-bar"></div>
<div class="logo-pill" style="left:75px;top:4263px;width:252px;height:78px">BRISK The Answer</div>
<p class="abs" style="left:366px;top:4292px;font-size:14px;color:var(--white)">Copyright © 2025 Company Name – All rights reserved</p>
<p class="abs" style="left:856px;top:4292px;font-size:14px;color:var(--white)">Legal Notices &nbsp;|&nbsp; Privacy Policy</p>

</body>
</html>
```